New website for concierge mobile medical service

new website for business:
WEBSITE REQUEST LIST:
Luxury product look.
Professional. Clean & simple, NO stock people photos. Graphics OK.
Black and white text.

```html
<!DOCTYPE html>
<html lang="en">
<head>
<meta charset="utf-8">
<title>Pricing · Veyra Health</title>
<link rel="stylesheet" href="https://fonts.googleapis.com/css2?family=Lato:wght@400;700;900&family=Fira+Sans:wght@400;500;700&display=swap">
<style>
:root{
  --ink:#1d1d1d;
  --white:#ffffff;
  --purple:#5b5ba8;
  --navy:#0b2a3c;
  --teal-dark:#104a63;
  --card-top:#3f5aa8;
  --card-bottom:#8478b8;
  --cyan:#5fe0ea;
  --subscribe-bg:#1a86a3;
  --subscribe-btn:#8acfd8;
  --footer-bg:#1e1e1e;
}
*{box-sizing:border-box;margin:0;padding:0}
html,body{width:1167px;height:1200px;overflow:hidden;background:var(--white)}
body{position:relative;font-family:"Lato",sans-serif;color:var(--ink)}
.abs{position:absolute}

/* header */
.site-header{position:absolute;left:0;top:0;width:1167px;height:104px;background:var(--white);z-index:2}
.brand{position:absolute;left:140px;top:46px;display:flex;align-items:center;gap:10px}
.brand-dot{width:34px;height:34px;border-radius:50%;background:var(--navy)}
.brand-name{font-family:"Lato",sans-serif;font-weight:700;font-size:20px;color:var(--navy)}
.phone{position:absolute;left:863px;top:16px;display:flex;align-items:center;gap:12px}
.phone-icon{width:31px;height:31px;background:var(--purple);display:flex;align-items:center;justify-content:center}
.phone-number{font-weight:700;font-size:19px;color:var(--purple)}
.main-nav a{position:absolute;top:74px;font-size:12px;font-weight:700;color:var(--ink);text-decoration:none;white-space:nowrap}
.main-nav .active::after{content:"";position:absolute;left:-9px;right:-13px;top:25px;height:5px;background:var(--navy)}

/* hero */
.hero{position:absolute;left:0;top:104px;width:1167px;height:257px;background:linear-gradient(90deg,#010306 0%,#03151f 35%,#0a3d5c 100%)}
.hero h1{position:absolute;left:140px;top:100px;font-size:44px;font-weight:900;color:var(--white);letter-spacing:.5px}
.hero-emblem{position:absolute;left:842px;top:32px}

/* intro */
.intro{position:absolute;left:0;top:402px;width:1167px;text-align:center;font-size:18.6px;line-height:26px;color:#222}

/* pricing cards */
.plan{position:absolute;top:480px;width:278px;height:257px;background:linear-gradient(180deg,var(--card-top),var(--card-bottom));text-align:center;color:var(--white);font-family:"Fira Sans",sans-serif}
.plan h2{margin-top:17px;font-size:23px;font-weight:500;letter-spacing:.3px}
.plan-icon{display:block;margin:11px auto 0;width:46px;height:46px;border-radius:50%;background:rgba(255,255,255,.85)}
.price{margin-top:14px;font-size:40px;font-weight:700;line-height:46px}
.price sup{font-size:20px;vertical-align:14px}
.price small{font-size:19px}
.plan-note{margin:14px auto 0;width:250px;font-size:15px;line-height:22px;font-weight:400}
.subscribe-btn{position:absolute;left:25px;top:233px;width:228px;height:46px;background:linear-gradient(180deg,var(--navy),var(--teal-dark));color:var(--white);font-size:19px;font-weight:500;line-height:46px;font-family:"Fira Sans",sans-serif}

/* subscribe */
.newsletter{position:absolute;left:0;top:824px;width:1167px;height:245px;background:linear-gradient(90deg,#1a86a3 0%,#1b7f9e 50%,#1682a3 100%)}
.newsletter h2{position:absolute;left:0;top:42px;width:1167px;text-align:center;font-family:"Fira Sans",sans-serif;font-weight:500;font-size:31px;color:var(--white);letter-spacing:.5px}
.field{position:absolute;top:100px;width:309px;height:43px;background:var(--white);font-size:12.5px;color:#333;padding-left:15px;line-height:43px}
.newsletter-btn{position:absolute;left:268px;top:152px;width:631px;height:43px;background:var(--subscribe-btn);color:var(--white);text-align:center;line-height:43px;font-size:15.5px;font-weight:700}

/* footer */
.site-footer{position:absolute;left:0;top:1069px;width:1167px;height:131px;background:var(--footer-bg);color:var(--white)}
.footer-nav a{position:absolute;top:23px;font-size:12px;font-weight:700;color:var(--white);text-decoration:none;white-space:nowrap}
.copyright{position:absolute;left:0;top:57px;width:1167px;text-align:center;font-size:11px}
.social{position:absolute;top:87px;width:16px;height:16px;border-radius:50%;background:var(--white)}
</style>
</head>
<body>

<header class="site-header">
  <div class="brand"><span class="brand-dot"></span><span class="brand-name">Veyra Health</span></div>
  <div class="phone">
    <span class="phone-icon">
      <svg width="16" height="16" viewBox="0 0 24 24"><path fill="#fff" d="M6.6 10.8c1.4 2.8 3.8 5.1 6.6 6.6l2.2-2.2c.3-.3.7-.4 1-.2 1.1.4 2.3.6 3.6.6.6 0 1 .4 1 1V20c0 .6-.4 1-1 1C10.6 21 3 13.4 3 4c0-.6.4-1 1-1h3.5c.6 0 1 .4 1 1 0 1.3.2 2.5.6 3.6.1.3 0 .7-.2 1z"/></svg>
    </span>
    <span class="phone-number">555-010-0199</span>
  </div>
  <nav class="main-nav">
    <a style="left:384px">HOME</a>
    <a style="left:461px">ABOUT US</a>
    <a style="left:563px">WHY VEYRA?</a>
    <a style="left:675px">SERVICE AREA</a>
    <a class="active" style="left:803px">OTHER</a>
    <a style="left:885px">FAQ</a>
    <a style="left:948px">CONTACT US</a>
  </nav>
</header>

<section class="hero">
  <h1>PRICING</h1>
  <svg class="hero-emblem" width="198" height="198" viewBox="0 0 198 198">
    <defs>
      <linearGradient id="ring" x1="0" y1="0" x2="1" y2="1">
        <stop offset="0" stop-color="#5fe0ea"/>
        <stop offset="0.6" stop-color="#4a78c8"/>
        <stop offset="1" stop-color="#8a7ccf"/>
      </linearGradient>
    </defs>
    <circle cx="99" cy="99" r="96" fill="none" stroke="url(#ring)" stroke-width="4"/>
    <circle cx="99" cy="99" r="80" fill="#0b3d5a" opacity="0.6" role="img" aria-label="Line illustration of a car with a medical emblem"/>
  </svg>
</section>

<p class="intro">Now accepting new patients with full mobile care starting March 1, 2020<br>New patients will have immediate access to Veyra Health mobile urgent care for $50/month.</p>

<article class="plan" style="left:141px">
  <h2>Individual</h2>
  <span class="plan-icon" role="img" aria-label="Single person icon"></span>
  <p class="price"><sup>$</sup>300/<small>mo.</small></p>
  <div class="subscribe-btn">Subscribe Today</div>
</article>
<article class="plan" style="left:445px">
  <h2>Married Couple</h2>
  <span class="plan-icon" role="img" aria-label="Couple icon"></span>
  <p class="price"><sup>$</sup>400/<small>mo.</small></p>
  <div class="subscribe-btn">Subscribe Today</div>
</article>
<article class="plan" style="left:749px">
  <h2>Child with Adult</h2>
  <span class="plan-icon" role="img" aria-label="Adult with child icon"></span>
  <p class="price"><sup>$</sup>75/<small>ea.mo.</small></p>
  <p class="plan-note">Pricing is for each child added to an adult subscription</p>
  <div class="subscribe-btn">Subscribe Today</div>
</article>

<section class="newsletter" role="img" aria-label="Subscribe section over a teal medical pattern background">
  <h2>Subscribe</h2>
  <div class="field" style="left:268px">Enter Name</div>
  <div class="field" style="left:590px">Enter Email Address</div>
  <div class="newsletter-btn">SUBSCRIBE NOW</div>
</section>

<footer class="site-footer">
  <nav class="footer-nav">
    <a style="left:293px">HOME</a>
    <a style="left:370px">ABOUT US</a>
    <a style="left:472px">WHY VEYRA?</a>
    <a style="left:586px">SERVICE AREA</a>
    <a style="left:713px">OTHER</a>
    <a style="left:794px">CONTACT US</a>
  </nav>
  <p class="copyright">Copyright © 2019.&nbsp; Company Name&nbsp; All Rights Reserved</p>
  <span class="social" style="left:508px"></span>
  <span class="social" style="left:540px"></span>
  <span class="social" style="left:573px"></span>
  <span class="social" style="left:607px"></span>
  <span class="social" style="left:639px"></span>
</footer>

</body>
</html>
```